Homemaking training schools needs a Business Card design

Designer, Hello!

No special requirements, good-looking enough.
--------------------------------------------------------------------------

Name: Marcus Dole
Chairman
Tel: 0574-71948263
Mobile: 13857420916
Email: kelvora@mailnest.example
Web: www.prt2019.example
Add: No.258, LanpingJie, BeiyuanQu, Ningbo, Zhejiang

LOGO
Ningbo PRT Homemaking Training School

Target Market(s)

pregnant women, mothers, infants, the elderly and families, including cleaning, cooking, nursing training.

Industry/Entity Type

Business

Contact Information for Business Card

Name: Marcus Dole
Chairman
Tel: 0574-71948263
Mobile: 13857420916
Email: kelvora@mailnest.example
Web: www.prt2019.example

LOGO

Font styles to use
Serif
Sans Serif
Decorative

Requirements
Nice to have
• Feels: clean, specifications, safety, comfort, warmth and happiness.

```html
<!DOCTYPE html>
<html lang="en">
<head>
<meta charset="utf-8">
<title>PeiRunTang Business Card</title>
<link rel="stylesheet" href="https://fonts.googleapis.com/css2?family=Open+Sans:wght@400;700&display=swap">
<style>
  :root {
    --brand-blue: #1f6db4;
    --brand-pink: #e5097f;
    --ink: #1d1d1d;
    --muted: #555;
    --card: #ffffff;
    --backdrop: #e9e6e2;
  }
  html, body { margin: 0; padding: 0; overflow: hidden; }
  body {
    width: 1200px; height: 1000px; position: relative;
    background: var(--backdrop);
    font-family: "Open Sans", sans-serif;
  }
  .card {
    position: absolute; left: 265px; width: 665px; height: 397px;
    background: var(--card); border-radius: 28px;
    box-shadow: 0 6px 16px rgba(0,0,0,.18);
  }
  .card--front { top: 73px; }
  .card--back { top: 533px; }

  .brand__name {
    position: absolute; left: 0; width: 100%; text-align: center;
    font-family: "Open Sans", sans-serif; font-weight: 700; font-size: 58px;
    color: var(--brand-blue); line-height: 1; letter-spacing: -0.5px;
  }
  .brand__tagline {
    position: absolute; left: 0; width: 100%; text-align: center;
    font-size: 22px; color: #333; line-height: 1;
  }

  .card--front .brand__name { top: 112px; }
  .card--front .brand__tagline { top: 182px; }

  .card--back .brand__name { top: 186px; }
  .card--back .brand__tagline { top: 256px; }

  .person {
    position: absolute; right: 350px; top: 252px; text-align: right;
    color: var(--ink);
  }
  .person__name { font-weight: 700; font-size: 22px; color: var(--brand-blue); line-height: 1.1; }
  .person__title { font-size: 15px; color: var(--brand-pink); line-height: 1.2; margin-bottom: 12px; }
  .person__address { font-size: 16px; line-height: 24px; }

  .divider {
    position: absolute; left: 332px; top: 255px; width: 2px; height: 92px;
    background: var(--ink);
  }

  .contacts {
    position: absolute; left: 350px; top: 254px; margin: 0; padding: 0;
    list-style: none; font-size: 16.5px; color: var(--ink);
  }
  .contacts li { display: flex; align-items: center; height: 24.5px; gap: 7px; }
  .contacts svg { width: 14px; height: 14px; fill: var(--brand-blue); flex: none; }

  .back-web {
    position: absolute; left: 0; width: 100%; top: 348px; text-align: center;
    font-size: 16px; color: var(--muted); letter-spacing: .3px;
  }
</style>
</head>
<body>

<section class="card card--front">
  <div class="brand__name">PeiRunTang</div>
  <div class="brand__tagline">Training &amp; Services</div>

  <div class="person">
    <div class="person__name">Marcus Dole</div>
    <div class="person__title">Chairman</div>
    <div class="person__address">258, LanpingJie, BeiyuanQu,<br>Ningbo, Zhejiang</div>
  </div>

  <div class="divider"></div>

  <ul class="contacts">
    <li>
      <svg viewBox="0 0 14 14" aria-hidden="true"><path d="M4 0h6a1 1 0 0 1 1 1v12a1 1 0 0 1-1 1H4a1 1 0 0 1-1-1V1a1 1 0 0 1 1-1zm0.6 1.6v8.6h4.8V1.6z"/></svg>
      0574-71948263
    </li>
    <li>
      <svg viewBox="0 0 14 14" aria-hidden="true"><path d="M1 5c0-2 3-3 6-3s6 1 6 3v1h-3V5H4v1H1zM3 7h8l2 5H1zm4 1.5a1.5 1.5 0 1 0 0 3a1.5 1.5 0 0 0 0-3z"/></svg>
      13857420916
    </li>
    <li>
      <svg viewBox="0 0 14 14" aria-hidden="true"><path d="M1 3h12v8H1zm1 1v.3l5 3.4 5-3.4V4zm0 1.6V10h10V5.6L7 9z"/></svg>
      kelvora@mailnest.example
    </li>
    <li>
      <svg viewBox="0 0 14 14" aria-hidden="true"><path d="M7 1a6 6 0 1 0 0 12A6 6 0 0 0 7 1zm0 1.3c.8 0 1.6 1.4 1.9 3.2H5.1C5.4 3.7 6.2 2.3 7 2.3zM2.4 6.8h2.5c0 .9.1 1.7.3 2.5H2.9a4.7 4.7 0 0 1-.5-2.5zm6.7 0h2.5c0 .9-.2 1.7-.5 2.5H8.8c.2-.8.3-1.6.3-2.5zM6.2 6.8h1.6c0 .9-.1 1.7-.3 2.5H6.5c-.2-.8-.3-1.6-.3-2.5z"/></svg>
      www.prt2019.example
    </li>
  </ul>
</section>

<section class="card card--back">
  <div class="brand__name">PeiRunTang</div>
  <div class="brand__tagline">Training &amp; Services</div>
  <div class="back-web">www.prt2019.example</div>
</section>

</body>
</html>
```